Marwick Law Letterhead

We need a new letterhead design for a Law Firm. The address for the law firm is 1475 Calloway Street, Suite 210, Houston, Texas 77041. Phone Number: 832-361-9027; Fax Number: 832-614-7359. The logo is uploaded to the project.

```html
<!DOCTYPE html>
<html lang="en">
<head>
<meta charset="utf-8">
<title>Marwick Law Letterhead</title>
<link href="https://fonts.googleapis.com/css2?family=Roboto:wght@400;500&display=swap" rel="stylesheet">
<style>
  :root {
    --navy: #15295b;
    --red: #c9202b;
    --red-deep: #8e1119;
    --ink: #333333;
    --paper: #f5f5f5;
    --backdrop: #e2e2e2;
  }
  * { margin: 0; padding: 0; box-sizing: border-box; }
  html, body {
    width: 1069px; height: 1200px; overflow: hidden;
    background: var(--backdrop);
    font-family: "Roboto", Arial, sans-serif;
    color: var(--ink);
  }
  .letterhead {
    position: absolute; left: 110px; top: 0;
    width: 848px; height: 1200px;
    background: var(--paper);
  }
  .brand {
    position: absolute; left: 47px; top: 70px;
    display: flex; align-items: center; gap: 12px;
  }
  .brand-mark { width: 18px; height: 18px; background: var(--navy); }
  .brand-name {
    font-size: 38px; font-weight: 500; color: var(--navy); letter-spacing: 0.5px;
  }
  .contact {
    position: absolute; right: 47px; top: 83px;
    list-style: none; font-size: 17px; line-height: 27px; color: #222;
  }
  .contact li { display: flex; align-items: center; justify-content: flex-end; gap: 6px; }
  .contact svg { width: 14px; height: 14px; fill: var(--red); }
  .recipient {
    position: absolute; left: 47px; top: 339px;
    font-size: 16px; line-height: 24.5px; font-style: normal;
  }
  .letter-para {
    position: absolute; left: 47px; width: 754px;
    font-size: 16px; line-height: 24.5px;
    text-align: justify; hyphens: auto;
  }
  .para-one { top: 454px; }
  .para-two { top: 602px; }
  .para-three { top: 746px; }
  .closing {
    position: absolute; left: 47px; top: 860px; font-size: 16px;
  }
  .signature {
    position: absolute; left: 47px; top: 898px; width: 155px; height: 62px;
    background: linear-gradient(90deg, #e6e6e6, #ededed);
    border-radius: 4px;
  }
  .footer-band {
    position: absolute; left: 0; top: 1124px; width: 848px; height: 39px;
    display: flex;
  }
  .footer-address {
    width: 598px; height: 100%; background: var(--navy);
    display: flex; align-items: center; gap: 8px; padding-left: 47px;
    color: #fff; font-size: 17px;
  }
  .footer-address svg { width: 12px; height: 17px; fill: #fff; }
  .footer-accent {
    flex: 1; background: linear-gradient(90deg, var(--red-deep), var(--red));
  }
</style>
</head>
<body>
  <main class="letterhead">
    <header>
      <div class="brand">
        <span class="brand-mark"></span>
        <span class="brand-name">Marwick Law</span>
      </div>
      <ul class="contact">
        <li>
          <svg viewBox="0 0 16 16" aria-hidden="true"><path d="M1 6c0-2 3-4 7-4s7 2 7 4v1h-4V5.5H5V7H1zM3 8h10l1 6H2z"/></svg>
          832-361-9027
        </li>
        <li>
          <svg viewBox="0 0 16 16" aria-hidden="true"><path d="M4 1h8v4H4zM1 6h14v6h-3v3H4v-3H1zM5 10v4h6v-4z"/></svg>
          832-614-7359
        </li>
      </ul>
    </header>

    <address class="recipient">
      Mr/s<br>First Name and Last Name<br>Company Name<br>Address
    </address>

    <p class="letter-para para-one">Lorem Ipsum is simply dummy text of the printing and typesetting industry. Lorem Ipsum has been the industry's standard dummy text ever since the 1500s, when an unknown printer took a galley of type and scrambled it to make a type specimen book. It has survived not only five centuries, but also the leap into electronic typesetting, remaining essentially unchanged. It was popularised in the 1960s with the release of Typeline sheets containing Lorem Ipsum passages.</p>
    <p class="letter-para para-two">he standard chunk of Lorem Ipsum used since the 1500s is reproduced below for those interested. Sections 1.10.32 and 1.10.33 from "de Finibus Bonorum et Malorum" by Aurel Vantis are also reproduced in their exact original form, accompanied by English versions from the 1914 translation by H. Ellery. Lorem ipsum dolor sit amet, consectetur adipiscing elit, sed do eiusmod tempor incididunt ut labore et dolore magna aliqua.</p>
    <p class="letter-para para-three">It is a long established fact that a reader will be distracted by the readable content of a page when looking at its layout. The point of using Lorem Ipsum is that it has a more-or-less normal distribution of letters, as opposed to using 'Content here, content here', making it look like readable English. Many desktop publishing packages and web page editors now .</p>

    <p class="closing">Your Sincerely,</p>
    <div class="signature" role="img" aria-label="Handwritten signature"></div>

    <footer class="footer-band">
      <div class="footer-address">
        <svg viewBox="0 0 12 17" aria-hidden="true"><path d="M6 0a6 6 0 0 0-6 6c0 4.5 6 11 6 11s6-6.5 6-11a6 6 0 0 0-6-6zm0 8.5A2.5 2.5 0 1 1 6 3.5a2.5 2.5 0 0 1 0 5z"/></svg>
        1475 Calloway Street, Suite 210, Houston, Texas 77041
      </div>
      <div class="footer-accent"></div>
    </footer>
  </main>
</body>
</html>
```